Legal firm website redesign

Existing site for Sydney CBD lawyer needs clean and professional redesign - http://brintonlaw.com.au

The site will be viewed by a wide range of users: businesses, individuals, referral partners and other lawyers.

Please see the list of must haves for further details

Target Market(s)

Businesses, individuals, referral partners and other lawyers

Industry/Entity Type

Lawyer

Requirements
Must have
• Prominent display of phone number.
List of services down the left hand side of the site (5x services or so).
Search box in header.
Please use the greys and blues from the existing header.
New header must include the wording "Efficiency - Fulfillment - Integrity - Teamwork"

```html
<!DOCTYPE html>
<html lang="en">
<head>
<meta charset="utf-8">
<title>Brinton Law</title>
<link rel="stylesheet" href="https://fonts.googleapis.com/css2?family=Source+Sans+3:wght@400;600;700&family=Arimo:wght@400;700&display=swap">
<style>
:root{
  --header-grey:#5c5c5c;
  --nav-blue:#1a6aa6;
  --nav-blue-light:#3b8ccc;
  --brand-blue:#155f96;
  --text-grey:#555;
  --slide-text:#6b6b6b;
  --page-bg:#f6f6f6;
  --footer-grey:#5e5e5e;
  --footer-text:#e2e2e2;
  --footer-muted:#c8c8c8;
  --white:#fff;
}
*{box-sizing:border-box;margin:0;padding:0}
html,body{width:1200px;height:995px;overflow:hidden}
body{position:relative;background:var(--page-bg);font-family:"Source Sans 3",sans-serif;color:var(--text-grey)}
.site-header{position:absolute;left:0;top:0;width:1200px;height:111px;background:var(--header-grey)}
.brand{position:absolute;left:124px;top:26px;font-size:44px;font-weight:600;color:var(--white);letter-spacing:-0.5px}
.call{position:absolute;left:816px;top:8px;display:flex;align-items:center;gap:10px;font-family:"Arimo",sans-serif;font-weight:700;font-size:19px;color:var(--white)}
.nav{position:absolute;left:0;top:111px;width:1200px;height:47px;background:var(--nav-blue);border-top:3px solid var(--nav-blue-light);box-shadow:0 2px 3px rgba(0,0,0,.3)}
.nav a{position:absolute;top:8px;height:27px;line-height:27px;font-size:16px;color:var(--white);text-decoration:none}
.nav .active{left:123px;width:74px;text-align:center;background:linear-gradient(#a9a9a9,#7d7d7d);border-radius:3px}
.search{position:absolute;left:880px;top:11px;width:199px;height:25px;background:#dfeefa;border:1px solid #b7cfe2}
.search span{position:absolute;left:8px;top:3px;font-size:14px;color:#555}
.search svg{position:absolute;right:6px;top:2px}
.content{position:absolute;left:111px;top:158px;width:979px;height:594px;background:var(--white)}
.slider{position:absolute;left:141px;top:189px;width:921px;height:308px;border:1px solid #c9c9c9;border-radius:5px;background:var(--white);overflow:hidden;box-shadow:0 1px 3px rgba(0,0,0,.12)}
.values{height:42px;background:#e3e3e3;border-bottom:1px solid #d0d0d0;position:relative}
.values span{position:absolute;top:7px;font-size:24px;font-weight:700;color:var(--brand-blue);transform:translateX(-50%)}
.slide-art{position:absolute;left:57px;top:50px;width:352px;height:245px;border-radius:4px;background:linear-gradient(135deg,#e4f2fb,#a9d6f2)}
.slide-copy{position:absolute;left:462px;top:106px;width:440px;font-size:19px;line-height:24px;color:var(--slide-text)}
.read-more{position:absolute;left:462px;top:199px;width:138px;height:38px;border:1px solid #c4c4c4;border-radius:3px;background:linear-gradient(#f4f4f4,#dcdcdc);font-size:14px;letter-spacing:.5px;color:#666;line-height:36px;padding-left:17px}
.read-more i{position:absolute;right:0;top:4px;width:24px;height:28px;border-left:1px solid #c4c4c4;font-style:normal;font-size:11px;text-align:center;line-height:28px}
.arrow{position:absolute;top:317px}
.about-title{position:absolute;left:139px;top:523px;font-size:23px;font-weight:600;color:var(--brand-blue)}
.about-body{position:absolute;left:141px;top:564px;width:920px;font-size:13.5px;line-height:18px;color:var(--text-grey)}
.about-body p{margin-bottom:18px}
.learn{position:absolute;left:978px;top:709px;font-size:14px;font-weight:600;color:var(--brand-blue)}
.footer{position:absolute;left:0;top:752px;width:1200px;height:206px;background:var(--footer-grey);font-family:"Arimo",sans-serif}
.footer-brand{position:absolute;left:138px;top:17px;font-family:"Source Sans 3",sans-serif;font-size:44px;font-weight:600;color:#7a7a7a}
.footer-email{position:absolute;left:145px;top:79px;font-size:14px;color:var(--footer-muted)}
.services{position:absolute;left:145px;top:108px;list-style:none;font-size:13px;line-height:18px;color:var(--footer-text)}
.services li::before{content:"›";margin-right:6px;color:var(--nav-blue-light);font-weight:700}
.col-title{position:absolute;top:25px;font-size:15px;font-weight:700;color:var(--white)}
.col{position:absolute;font-size:13.5px;color:var(--footer-text)}
.links{left:451px;top:66px;line-height:20px}
.address{left:594px;top:56px;line-height:23px;color:var(--footer-muted)}
.phones{left:754px;top:58px;line-height:23px;color:var(--footer-muted)}
.legal-bar{position:absolute;left:0;top:958px;width:1200px;height:37px;background:var(--white);font-family:"Arimo",sans-serif;font-size:14px;color:#333}
.legal-bar .copy{position:absolute;left:129px;top:10px}
.legal-bar .policy{position:absolute;right:131px;top:10px}
</style>
</head>
<body>
<header class="site-header">
  <div class="brand">brinton law</div>
  <div class="call">
    <svg width="30" height="40" viewBox="0 0 36 44"><path d="M9 3c-5 2-7 7-6 13 2 10 8 20 16 25 4 2 8 2 11-1l-6-9-5 2c-4-4-7-10-8-15l5-2z" fill="#f0b068"/></svg>
    <span>Call Us on (022) 8340 2675</span>
  </div>
</header>
<nav class="nav">
  <a class="active">Home</a>
  <a style="left:219px">About Us</a>
  <a style="left:323px">Areas of Law</a>
  <a style="left:450px">Publication</a>
  <a style="left:568px">Contact</a>
  <div class="search"><span>Search</span>
    <svg width="26" height="20" viewBox="0 0 26 20"><circle cx="9" cy="8" r="6" fill="none" stroke="#444" stroke-width="2.5"/><path d="M13 12l9 7" stroke="#444" stroke-width="3.5" stroke-linecap="round"/></svg>
  </div>
</nav>
<main class="content"></main>
<section class="slider">
  <div class="values">
    <span style="left:146px">EFFICIENCY</span>
    <span style="left:369px">FULFILLMENT</span>
    <span style="left:591px">INTEGRITY</span>
    <span style="left:799px">TEAMWORK</span>
  </div>
  <div class="slide-art" role="img" aria-label="Illustration of a hand reaching out of a computer screen holding an envelope beside a globe"></div>
  <p class="slide-copy">Lorem ipsum dolor sit amet, consectetur adipiscing elit. Morbi iaclis pretium leo, eu faucibus urna ultricies non. Vestibulum eget augue quam, nec tristique neque.</p>
  <div class="read-more">READ MORE<i>&#8964;</i></div>
</section>
<svg class="arrow" style="left:114px" width="50" height="50" viewBox="0 0 50 50"><circle cx="25" cy="25" r="23" fill="#f3f3f3" stroke="#bbb" stroke-width="2"/><path d="M28 15l-10 10 10 10M34 15l-10 10 10 10" fill="none" stroke="#999" stroke-width="2"/></svg>
<svg class="arrow" style="left:1036px" width="50" height="50" viewBox="0 0 50 50"><circle cx="25" cy="25" r="23" fill="#f3f3f3" stroke="#bbb" stroke-width="2"/><path d="M22 15l10 10-10 10M16 15l10 10-10 10" fill="none" stroke="#999" stroke-width="2"/></svg>
<h1 class="about-title">About Brinton Law</h1>
<div class="about-body">
  <p>Brinton Law is a dynamic commercial law firm in the CBD of Sydney providing services to corporate, small business and private clients.</p>
  <p>Brinton Law brings together over 30 years of experience in legal practice.</p>
  <p>The strong focus of the firm is on commercial law and estate planning.</p>
  <p>Brinton Law is committed to providing quality legal services in helping its clients achieve their objectives by providing a proactive understanding of its clients' businesses and creative legal solutions.</p>
</div>
<a class="learn">Learn More...</a>
<footer class="footer">
  <div class="footer-brand">brinton law</div>
  <div class="footer-email">Email: info@brintonlaw.com.au</div>
  <ul class="services">
    <li>Commercial Law</li>
    <li>Estate Planning</li>
    <li>Business Structures</li>
    <li>Property Law</li>
    <li>Dispute Resolution</li>
  </ul>
  <div class="col-title" style="left:451px">Company</div>
  <div class="col links">Home<br>About Us<br>Area of Law<br>Our People<br>Publication<br>Contact Us</div>
  <div class="col-title" style="left:594px">Contact Us</div>
  <div class="col address">Tom Hadley<br>Lot 9 Carrow Street,<br>Glenbrook, SA, 5160<br>PO Box 248,<br>Glenbrook, SA, 5160</div>
  <div class="col phones">Phone Work/Mobile: 0418552043<br>Phone: 08 8471 3306<br>Fax: 08 84713307<br>Email: tom@hadleyfencing.com</div>
</footer>
<div class="legal-bar">
  <span class="copy">© 2000-2012, brintonlaw All Rights Reserved.</span>
  <span class="policy">Privacy Policy | Site User Terms and Conditions</span>
</div>
</body>
</html>
```